Business Cards for new orthopaedic surgery practice

My husband and I are starting our own orthopaedic surgery practice. We are looking for a business card that is uniform, but one will have my name/title and the other will have his. You can just create one design with my name on it for now. But when I choose your design as the winning design I will ask that you add another copy with his name/title.

We are looking for classy, simple, elite all in one. We like dark blues/a little gold/yellow. Something that goes with our logo. We want our logo incorporated. Here is all the info you need:
Business name: RV Bone & Vitality Center
Location: 38517 North Willowmere Ave
Harbor Glen, FL 33490
Phone: 954-218-4063
Fax: 954-582-7341
Email: info@myrvbonecare.example

Names: Lydia Vance, M.D.
Board Certified Hand and Upper Extremity Surgeon

Ebo Dansu, M.D.
Board Certified Hip & Knee Replacement/General Orthopaedic Surgeon

Can decide what you want to put on the back. Maybe a slogan:
Steady Hands. Devoted to You

I am just going to upload our logo. The only thing is if we select you as the winning design, the location, and phone numbers may change. We will need your help to update that once fully solidified.

Industry/Entity Type

Medical

Contact Information for Business Card

Colors
0054AA
0677BA
7BADD7
CADEEF
E8F1F8
0094D4
00A9DD
6FCCEA
C7EBF8
E9F6FB

Requirements
Must have
• class, appeal,
Should not have
• We want to air on the side of masculine if we are looking at masculine vs. feminine feel. But we still want it classy, sophisticated, and something we will love

```html
<!DOCTYPE html>
<html lang="en">
<head>
<meta charset="utf-8">
<title>RV Bone &amp; Vitality Center – Business Card</title>
<link rel="stylesheet" href="https://fonts.googleapis.com/css2?family=Montserrat:wght@400;500;600;700&display=swap">
<style>
  :root {
    --navy: #1b2a55;
    --navy-deep: #1a2850;
    --gold: #c9a45c;
    --ink: #1f2433;
    --white: #ffffff;
    --stage: #eceef2;
    --faint: rgba(120, 140, 200, 0.28);
  }
  * { margin: 0; padding: 0; box-sizing: border-box; }
  html, body {
    width: 916px; height: 1200px; overflow: hidden;
    background: var(--stage);
    font-family: "Montserrat", Arial, sans-serif;
    color: var(--ink);
  }
  .canvas { position: relative; width: 916px; height: 1200px; }
  .card {
    position: absolute; left: 73px; width: 772px; height: 460px;
    border-radius: 22px; overflow: hidden;
  }
  .card-front { top: 108px; background: var(--white); }
  .card-back { top: 640px; background: var(--navy-deep); }

  .brand-mark {
    position: absolute; left: 45px; top: 26px; width: 138px; height: 138px;
    border: 2px solid var(--navy); border-radius: 50%;
    display: flex; align-items: center; justify-content: center; text-align: center;
    font-weight: 700; font-size: 15px; line-height: 1.25; color: var(--navy);
    padding: 14px;
  }
  .name-bar {
    position: absolute; left: 0; top: 193px; width: 21px; height: 40px;
    background: var(--navy);
  }
  .holder { position: absolute; left: 36px; top: 191px; }
  .holder-name { font-size: 26px; font-weight: 700; color: var(--navy); }
  .holder-name .credential { color: var(--gold); }
  .holder-title { margin-top: 6px; font-size: 16px; line-height: 1.3; color: var(--ink); }
  .address { position: absolute; left: 36px; top: 290px; font-size: 16px; line-height: 1.35; }
  .contacts { position: absolute; left: 38px; top: 349px; list-style: none; font-size: 16px; }
  .contacts li { display: flex; align-items: center; gap: 8px; height: 26px; }
  .contacts svg { width: 14px; height: 14px; fill: var(--gold); flex: none; }

  .brand-feature {
    position: absolute; left: 364px; top: 20px; width: 390px; height: 420px;
    display: flex; align-items: center;
    font-size: 62px; font-weight: 700; line-height: 1.05; color: var(--navy);
  }

  .back-ring {
    position: absolute; left: 226px; top: 70px; width: 320px; height: 320px;
    border: 2px solid var(--faint); border-radius: 50%;
  }
  .back-brand {
    position: absolute; left: 226px; top: 70px; width: 320px; height: 320px;
    display: flex; align-items: center; justify-content: center; text-align: center;
    font-size: 34px; font-weight: 700; line-height: 1.15; color: var(--faint);
    padding: 40px;
  }
  .slogan {
    position: absolute; left: 0; right: 0; top: 418px; text-align: center;
    font-size: 17px; font-weight: 500; color: var(--white);
  }
</style>
</head>
<body>
<main class="canvas">
  <section class="card card-front">
    <div class="brand-mark">RV Bone &amp; Vitality Center</div>

    <span class="name-bar"></span>
    <div class="holder">
      <h1 class="holder-name">Lydia Vance, <span class="credential">M.D.</span></h1>
      <p class="holder-title">Board Certified Hand and<br>Upper Extremity Surgeon</p>
    </div>

    <p class="address">38517 North Willowmere Ave<br>Harbor Glen, FL 33490</p>

    <ul class="contacts">
      <li>
        <svg viewBox="0 0 16 16" aria-hidden="true"><path d="M1 6c0-2 3-3 7-3s7 1 7 3v1h-3V5.5C11 5 9.5 5 8 5s-3 0-4 .5V7H1z M3 8h10l1 6H2z"/></svg>
        954-218-4063
      </li>
      <li>
        <svg viewBox="0 0 16 16" aria-hidden="true"><path d="M4 1h8v4H4z M1 6h14v6h-3v3H4v-3H1z M5 10v4h6v-4z"/></svg>
        954-582-7341
      </li>
      <li>
        <svg viewBox="0 0 16 16" aria-hidden="true"><path d="M1 3h14v1.5L8 9 1 4.5z M1 6l7 4.5L15 6v7H1z"/></svg>
        info@myrvbonecare.example
      </li>
    </ul>

    <div class="brand-feature">RV Bone &amp; Vitality Center</div>
  </section>

  <section class="card card-back">
    <div class="back-ring"></div>
    <div class="back-brand">RV Bone &amp; Vitality Center</div>
    <p class="slogan">Steady Hands. Devoted to You</p>
  </section>
</main>
</body>
</html>
```